New Wrestling company needs a website

We need a website design for a new wrestling company in Australia that will be running 3-4 events per year. Wrestling company is Summit Grip Wrestling (SGW).

The design of the logo is in place and can be provided, and I have purchased the website domain.

A detailed description of the intent and purpose of this company can be provided.

The aim would be to have around 5 specific pages on SGW, with two standard “about” and “contact” pages. E.g.
- About SGW (focus and purpose of the company)
- SGW Events (specific focus on events run by SGW)
- SGW News (news and stories on wrestling’s across Oceania)
- SGW Media (where to watch SGW and our partners))
- SGW Partners and Sponsors (partner and affiliate information)
- SGW Power Rankings (top 10 ranked wrestlers from Oceania which is updated weekly)
- SGW fans (highlighting how to become part of SGW as a fan)
- Contact SGW
Updates

The logo design should now be included in the brief, please feel free to reach out to me directly if you can't access it or require any other information.

Target Market(s)

Wrestling Fans

Industry/Entity Type

Sport / Wrestling

Coding

Coded - Design and coding required

Number of Pages Required

5+ page

Requirements
Must have
• A Wrestling and or Sports feel to the website design

```html
<!DOCTYPE html>
<html lang="en">
<head>
<meta charset="utf-8">
<title>Summit Grip Wrestling</title>
<link href="https://fonts.googleapis.com/css2?family=Rajdhani:wght@500;600;700&family=Roboto:wght@400;500&display=swap" rel="stylesheet">
<style>
:root{
  --bg:#0a0c11;
  --bg-2:#10141b;
  --panel:#1a1d24;
  --blue:#1f8fe3;
  --blue-bright:#3aa9ff;
  --white:#ffffff;
  --muted:#aeb4bf;
  --line:#2b303a;
}
*{box-sizing:border-box;margin:0;padding:0}
html,body{width:1200px;height:4792px;overflow:hidden}
body{background:var(--bg);color:var(--white);font-family:"Roboto",Arial,sans-serif;position:relative}
.abs{position:absolute}
h1,h2,h3,.brand,.nav a,.btn{font-family:"Rajdhani","Arial Narrow",sans-serif}
.btn{display:inline-block;background:var(--blue);color:var(--white);font-weight:700;font-size:20px;letter-spacing:1px;text-transform:uppercase;padding:14px 36px}
.photo{display:block}
p{color:var(--muted);font-size:15px;line-height:1.6}

/* header & hero */
.hero{left:0;top:0;width:1200px;height:760px;overflow:hidden;background:linear-gradient(180deg,#1a1c22,#0d0f14)}
.hero-photo{left:0;top:0;width:1200px;height:700px;background:linear-gradient(100deg,#14161c 0%,#3a2a24 45%,#6b5141 62%,#2c2a30 80%,#101217 100%)}
.topbar{left:0;top:0;width:1200px;height:96px;background:rgba(6,8,12,.55)}
.brand{left:108px;top:22px;font-size:44px;font-weight:700;color:var(--blue-bright);display:flex;align-items:center;gap:14px}
.brand .dot{width:18px;height:18px;border-radius:50%;background:var(--blue-bright)}
.nav{right:108px;top:40px;display:flex;gap:26px;align-items:center}
.nav a{color:var(--white);font-size:18px;font-weight:600;text-decoration:none}
.social{width:28px;height:28px;border:1px solid #fff}
.hero-title{left:108px;top:210px;font-size:78px;line-height:80px;font-weight:700;letter-spacing:2px;text-transform:uppercase}
.hero-title span{color:var(--blue-bright);display:block}
.hero-copy{left:108px;top:380px;width:460px;color:#e6e8ec}
.hero .btn{left:108px;top:478px}
.arrow-btn{width:40px;height:40px;border-radius:50%;background:rgba(0,0,0,.55);display:flex;align-items:center;justify-content:center}

/* section headings */
.eyebrow{font-size:20px;color:var(--muted);text-align:center;width:1200px;left:0}
.sec-title{font-size:48px;font-weight:700;color:var(--blue-bright);text-align:center;width:1200px;left:0}

/* welcome */
.welcome-bg{left:0;top:740px;width:1200px;height:780px;background:linear-gradient(180deg,#0c1017,#0a0c11)}
.welcome-frame{left:112px;top:832px;width:456px;height:472px;border:2px solid var(--line)}
.welcome-photo{left:132px;top:852px;width:428px;height:428px;background:linear-gradient(160deg,#2a2e35,#5a2a26 60%,#7a1b1b)}
.welcome-text{left:600px;top:890px;width:500px}
.welcome-text h3{font-size:34px;font-weight:600}
.welcome-text h2{font-size:46px;font-weight:700;color:var(--blue-bright);margin-bottom:20px}
.welcome-text .btn{margin-top:28px}

/* events */
.events-bg{left:0;top:1520px;width:1200px;height:700px;background:linear-gradient(180deg,#121419,#0c0e12)}
.event-card{width:306px;height:460px;background:var(--panel)}
.event-photo{width:306px;height:240px;border:4px solid #fff;background:linear-gradient(140deg,#3b3238,#7a4a3a 55%,#1b2a44)}
.event-date{left:16px;top:180px;width:56px;height:64px;background:var(--blue);font-size:13px;text-align:center;padding-top:12px;line-height:18px;font-weight:500}
.event-body{left:18px;top:262px;width:270px}
.event-body h3{font-family:"Roboto",sans-serif;font-size:15px;font-weight:500;margin-bottom:10px}
.event-body p{font-size:13px;line-height:1.5}

/* news */
.news-bg{left:0;top:2220px;width:1200px;height:820px;background:radial-gradient(ellipse at 78% 45%,#3a3c42 0%,#15171c 40%,#0a0c11 70%)}
.news-eyebrow{left:110px;top:2290px;font-size:38px;color:#dfe2e7}
.news-title{left:110px;top:2336px;font-size:54px;font-weight:700;color:var(--blue-bright)}
.news-item{left:110px;width:560px;height:150px}
.news-thumb{width:200px;height:148px;background:linear-gradient(150deg,#23324f,#6a3a30 60%,#1a1d24)}
.news-text{left:230px;top:4px;width:330px}
.news-text .date{font-size:12px;color:var(--blue-bright)}
.news-text h3{font-family:"Roboto",sans-serif;font-size:17px;font-weight:500;margin:8px 0}
.news-text p{font-size:13px;line-height:1.5}

/* media */
.media-bg{left:0;top:3040px;width:1200px;height:480px;background:linear-gradient(90deg,#0c0e12,#2a3a60 45%,#1a1d28 70%,#0c0e12)}
.play{left:560px;top:3180px;width:80px;height:80px;border-radius:50%;background:var(--blue)}
.track{left:110px;top:3480px;width:980px;height:22px;border:2px solid #5b616c;border-radius:11px}

/* power rankings */
.rank-bg{left:0;top:3520px;width:1200px;height:800px;background:
  radial-gradient(ellipse 520px 260px at 560px 380px,rgba(31,143,227,.22),transparent 70%),
  radial-gradient(ellipse 420px 200px at 320px 120px,rgba(31,143,227,.14),transparent 70%),
  linear-gradient(180deg,#0a0c11,#0d1726 50%,#0a0c11)}
.rank-photo{left:230px;top:3700px;width:180px;height:340px;background:linear-gradient(180deg,#3a2430,#6a2a5a 55%,#2a1a22)}
.rank-name{left:110px;top:4060px;font-size:34px;font-weight:700;color:var(--blue-bright)}
.rank-copy{left:110px;top:4110px;width:400px}
.rank-table{left:596px;top:3780px;width:494px;height:400px;border:2px solid var(--blue);box-shadow:0 0 24px rgba(31,143,227,.55);background:rgba(10,14,20,.85);padding:12px 14px}
.rank-row{height:62px;display:flex;align-items:center;justify-content:space-between;border-bottom:1px solid var(--line);padding:0 10px;font-size:16px;color:#e4e7ec}
.rank-row:last-child{border-bottom:none}

/* contact */
.contact-bg{left:0;top:4320px;width:1200px;height:320px;background:#0d0f13}
.contact-title{left:0;top:4396px;width:1200px;text-align:center;font-size:42px;font-weight:700}
.field{top:4512px;width:180px;height:56px;border:1px solid #5b616c;border-radius:4px;font-size:13px;color:var(--muted);padding:20px 12px}
.submit{left:912px;top:4512px;width:180px;height:56px;background:var(--blue);border-radius:4px;text-align:center;line-height:56px;font-family:"Rajdhani",sans-serif;font-weight:700;font-size:20px}

/* footer */
.footer{left:0;top:4640px;width:1200px;height:152px;background:#090a0d;border-top:1px solid var(--line)}
.footer-left{left:110px;top:4680px;font-size:13px;line-height:22px;color:#c9cdd4}
.footer-nav{right:110px;top:4696px;display:flex;gap:26px}
.footer-nav a{color:#c9cdd4;font-size:14px;text-decoration:none}
</style>
</head>
<body>

<!-- header / hero -->
<section class="hero abs">
  <div class="hero-photo abs photo" role="img" aria-label="Two wrestlers grappling in a ring under arena lights"></div>
  <div class="topbar abs"></div>
  <div class="brand abs"><span class="dot"></span>SGW</div>
  <nav class="nav abs">
    <a>About</a><a>Events</a><a>News</a><a>Media</a><a>Partners</a><a>Power Rankings</a><a>Fans</a><a>Contact</a>
    <span class="social"></span><span class="social"></span>
  </nav>
  <h1 class="hero-title abs">Summit Grip<span>Wrestling</span></h1>
  <p class="hero-copy abs">Lorem ipsum dolor sit amet, consectetur adipiscing elit, sed do eiusmod tempor incididunt ut labore et dolore magna aliqua. Ut enim ad minim veniam.</p>
  <a class="btn abs">Get Started</a>
  <div class="arrow-btn abs" style="left:28px;top:340px"><svg width="14" height="14"><path d="M10 2 4 7l6 5" stroke="#fff" stroke-width="2" fill="none"/></svg></div>
  <div class="arrow-btn abs" style="right:28px;top:340px"><svg width="14" height="14"><path d="M4 2l6 5-6 5" stroke="#fff" stroke-width="2" fill="none"/></svg></div>
  <svg class="abs" style="left:0;top:660px" width="1200" height="100"><polygon points="0,60 1200,10 1200,100 0,100" fill="#0c1017"/><polygon points="0,40 420,50 300,70 0,72" fill="var(--blue)"/><polygon points="0,72 300,70 0,90" fill="#0e3a66"/></svg>
</section>

<!-- welcome -->
<section>
  <div class="welcome-bg abs"></div>
  <div class="welcome-frame abs"></div>
  <div class="welcome-photo abs photo" role="img" aria-label="Two fighters sparring on a red training mat"></div>
  <div class="welcome-text abs">
    <h3>Welcome to</h3>
    <h2>Summit Grip Wrestling</h2>
    <p>Lorem ipsum dolor sit amet, consectetur adipiscing elit, sed do eiusmod tempor incididunt ut labore et dolore magna aliqua. Ut enim ad minim veniam, quis nostrud exercitation ullamco laboris nisi ut aliquip ex ea commodo consequat. Duis aute irure dolor in reprehenderit in voluptate velit esse cillum dolore eu fugiat nulla pariatur. Excepteur sint occaecat cupidatat non proident, sunt in culpa qui officia deserunt.</p>
    <a class="btn">Read More</a>
  </div>
  <svg class="abs" style="left:0;top:1440px" width="1200" height="80"><polygon points="0,80 1200,20 1200,80" fill="#121419"/><polygon points="900,40 1200,26 1200,44" fill="var(--blue)"/></svg>
</section>

<!-- events -->
<section>
  <div class="events-bg abs"></div>
  <div class="eyebrow abs" style="top:1556px">Lorem ipsum</div>
  <h2 class="sec-title abs" style="top:1578px">Our Events</h2>
  <div class="arrow-btn abs" style="left:48px;top:1800px;border:2px solid #fff"><svg width="14" height="14"><path d="M10 2 4 7l6 5" stroke="#fff" stroke-width="2" fill="none"/></svg></div>
  <div class="arrow-btn abs" style="right:48px;top:1800px;border:2px solid #fff"><svg width="14" height="14"><path d="M4 2l6 5-6 5" stroke="#fff" stroke-width="2" fill="none"/></svg></div>

  <article class="event-card abs" style="left:112px;top:1664px">
    <div class="event-photo photo" role="img" aria-label="Wrestler in red tights lifting an opponent"></div>
    <div class="event-date abs">Dec<br>17</div>
    <div class="event-body abs"><h3>Lorem ipsum dolor sit amet, consectetur adipiscing elit.</h3><p>Sed do eiusmod tempor incididunt ut labore et dolore magna aliqua. Ut enim ad minim veniam quis nostrud exercitation ullamco laboris nisi ut aliquip ex ea commodo.</p>
    <svg width="18" height="14" style="margin-top:12px"><path d="M1 7h14M10 2l5 5-5 5" stroke="var(--blue-bright)" stroke-width="2" fill="none"/></svg></div>
  </article>
  <article class="event-card abs" style="left:448px;top:1664px">
    <div class="event-photo photo" role="img" aria-label="Two wrestlers locked in a hold on the mat"></div>
    <div class="event-date abs">Dec<br>17</div>
    <div class="event-body abs"><h3>Lorem ipsum dolor sit amet, consectetur adipiscing elit.</h3><p>Sed do eiusmod tempor incididunt ut labore et dolore magna aliqua. Ut enim ad minim veniam quis nostrud exercitation ullamco laboris nisi ut aliquip ex ea commodo.</p>
    <svg width="18" height="14" style="margin-top:12px"><path d="M1 7h14M10 2l5 5-5 5" stroke="var(--blue-bright)" stroke-width="2" fill="none"/></svg></div>
  </article>
  <article class="event-card abs" style="left:782px;top:1664px">
    <div class="event-photo photo" role="img" aria-label="Wrestler shouting during a match"></div>
    <div class="event-date abs">Dec<br>17</div>
    <div class="event-body abs"><h3>Lorem ipsum dolor sit amet, consectetur adipiscing elit.</h3><p>Sed do eiusmod tempor incididunt ut labore et dolore magna aliqua. Ut enim ad minim veniam quis nostrud exercitation ullamco laboris nisi ut aliquip ex ea commodo.</p>
    <svg width="18" height="14" style="margin-top:12px"><path d="M1 7h14M10 2l5 5-5 5" stroke="var(--blue-bright)" stroke-width="2" fill="none"/></svg></div>
  </article>
  <svg class="abs" style="left:0;top:2160px" width="1200" height="70"><polygon points="0,20 1200,0 1200,30 0,60" fill="#0c0e12"/><polygon points="0,28 520,14 260,40 0,44" fill="var(--blue)"/></svg>
</section>

<!-- news -->
<section>
  <div class="news-bg abs photo" role="img" aria-label="Shadowed muscular wrestler with fists raised"></div>
  <div class="news-eyebrow abs">Lorem ipsum</div>
  <h2 class="news-title abs">Our Latest News</h2>
  <article class="news-item abs" style="top:2448px">
    <div class="news-thumb photo" role="img" aria-label="Wrestlers clashing in the ring"></div>
    <div class="news-text abs"><div class="date">Dec 17 2020</div><h3>Lorem ipsum dolor sit amet, consectetur</h3><p>Sed do eiusmod tempor incididunt ut labore et dolore magna aliqua. Ut enim ad minim veniam, quis nostrud.</p></div>
  </article>
  <article class="news-item abs" style="top:2620px">
    <div class="news-thumb photo" role="img" aria-label="Wrestler diving from the ropes"></div>
    <div class="news-text abs"><div class="date">Dec 17 2020</div><h3>Lorem ipsum dolor sit amet, consectetur</h3><p>Sed do eiusmod tempor incididunt ut labore et dolore magna aliqua. Ut enim ad minim veniam, quis nostrud.</p></div>
  </article>
  <article class="news-item abs" style="top:2800px">
    <div class="news-thumb photo" role="img" aria-label="Masked wrestler on the apron"></div>
    <div class="news-text abs"><div class="date">Dec 17 2020</div><h3>Lorem ipsum dolor sit amet, consectetur</h3><p>Sed do eiusmod tempor incididunt ut labore et dolore magna aliqua. Ut enim ad minim veniam, quis nostrud.</p></div>
  </article>
</section>

<!-- media -->
<section>
  <div class="media-bg abs photo" role="img" aria-label="Video still of two wrestlers mid-throw"></div>
  <div class="eyebrow abs" style="top:3090px">Lorem ipsum</div>
  <h2 class="sec-title abs" style="top:3112px">Our Media</h2>
  <div class="play abs"><svg width="80" height="80"><polygon points="32,24 58,40 32,56" fill="#fff"/></svg></div>
  <div class="abs" style="left:110px;top:3450px;font-size:12px;color:#c9cdd4">00:00</div>
  <div class="abs" style="right:110px;top:3450px;font-size:12px;color:#c9cdd4">10:00</div>
  <div class="track abs"></div>
  <div class="abs" style="left:108px;top:3476px;width:30px;height:30px;border-radius:50%;background:var(--blue)"></div>
</section>

<!-- power rankings -->
<section>
  <div class="rank-bg abs" role="img" aria-label="Dark arena backdrop with soft blue electric glow"></div>
  <div class="eyebrow abs" style="top:3610px">Lorem ipsum</div>
  <h2 class="sec-title abs" style="top:3632px">Power Rankings</h2>
  <div class="rank-photo abs photo" role="img" aria-label="Featured wrestler standing in purple gear"></div>
  <h3 class="rank-name abs">Riley Maddox</h3>
  <p class="rank-copy abs">Lorem ipsum dolor sit amet, consectetur adipiscing elit, sed do eiusmod tempor incididunt ut labore et dolore magna aliqua. Ut enim ad minim veniam.</p>
  <div class="rank-table abs">
    <div class="rank-row"><span>1. Riley Maddox</span><span>Lorem ipsum</span></div>
    <div class="rank-row"><span>2. Riley Maddox</span><span>Lorem ipsum</span></div>
    <div class="rank-row"><span>3. Riley Maddox</span><span>Lorem ipsum</span></div>
    <div class="rank-row"><span>4. Riley Maddox</span><span>Lorem ipsum</span></div>
    <div class="rank-row"><span>5. Riley Maddox</span><span>Lorem ipsum</span></div>
    <div class="rank-row"><span>6. Riley Maddox</span><span>Lorem ipsum</span></div>
  </div>
</section>

<!-- contact -->
<section>
  <div class="contact-bg abs"></div>
  <h2 class="contact-title abs">Contact Us Today</h2>
  <div class="field abs" style="left:110px">Name</div>
  <div class="field abs" style="left:310px">Email</div>
  <div class="field abs" style="left:510px">Phone</div>
  <div class="field abs" style="left:710px">Message</div>
  <div class="submit abs">SUBMIT</div>
</section>

<!-- footer -->
<footer>
  <div class="footer abs"></div>
  <div class="footer-left abs">© 2020 Summit Grip Wrestling<br>info@summitgripwrestling.com<br>Privacy Policy | Terms &amp; Conditions</div>
  <nav class="footer-nav abs"><a>About</a><a>Events</a><a>News</a><a>Media</a><a>Partners</a><a>Power Rankings</a><a>Fans</a><a>Contact</a></nav>
</footer>

</body>
</html>
```